Robotic Physical Therapy office needs a Grand Opening Flyer

We need a Grand Opening flyer design for a robotic physical therapy office named Kinetic Harbor Wellness. We would like it to have a clean, classy, upscale feeling that gives potential clients a V.I.P. feeling. We would like to use the colors black, gray, and yellow (logo will be uploaded).

Event: Thursday, June 1st, 2023 from 12pm-6pm
location: 58274 Pellham Ave, Bloomfield Hills, MI 48519

Industry/Entity Type

Physical therapy

Font styles to use
Script

Colors

Designer to choose colors to be used in the design.

Requirements
Nice to have
• More of a vip feel for the invite

```html
<!DOCTYPE html>
<html lang="en">
<head>
<meta charset="utf-8">
<title>Kinetic Harbor Wellness – Grand Opening</title>
<link rel="stylesheet" href="https://fonts.googleapis.com/css2?family=Poppins:wght@300;400;600;700;800&display=swap">
<style>
  :root {
    --ink: #2d2e35;
    --ink-deep: #26272d;
    --ink-soft: #3a3b43;
    --gold: #f5d928;
    --white: #ffffff;
  }
  * { margin: 0; padding: 0; box-sizing: border-box; }
  html, body { width: 865px; height: 1200px; overflow: hidden; background: var(--ink); }
  .flyer {
    position: relative;
    width: 865px;
    height: 1200px;
    background: var(--ink);
    font-family: "Poppins", sans-serif;
    color: var(--white);
    overflow: hidden;
  }
  .flyer__artwork {
    position: absolute;
    left: 20px; top: 150px;
    width: 820px; height: 1050px;
    background: radial-gradient(ellipse 55% 45% at 52% 42%, var(--ink-soft) 0%, rgba(58,59,67,0.55) 45%, rgba(45,46,53,0) 75%);
  }
  .flyer__frame {
    position: absolute;
    inset: 17px;
    border: 1px solid var(--gold);
  }
  .brand {
    position: absolute;
    top: 82px; left: 0; right: 0;
    display: flex; justify-content: center; align-items: center; gap: 14px;
  }
  .brand__dot {
    width: 22px; height: 22px; border-radius: 50%;
    background: var(--gold);
  }
  .brand__name {
    font-weight: 600; font-size: 38px; letter-spacing: 0.5px;
    color: var(--gold); line-height: 1;
  }
  .centered { position: absolute; left: 0; right: 0; text-align: center; line-height: 1; }
  .headline__grand { top: 272px; font-weight: 300; font-size: 132px; color: var(--gold); letter-spacing: -1px; }
  .headline__opening { top: 390px; font-weight: 800; font-size: 132px; color: var(--white); letter-spacing: -2px; }
  .date__weekday { top: 552px; font-weight: 400; font-size: 24px; color: var(--gold); letter-spacing: 9px; padding-left: 9px; }
  .date__month { top: 584px; font-weight: 700; font-size: 72px; color: var(--white); letter-spacing: -1px; }
  .date__day { top: 662px; font-weight: 800; font-size: 190px; color: var(--gold); }
  .date__year { top: 848px; font-weight: 300; font-size: 34px; color: var(--white); letter-spacing: 14px; padding-left: 14px; }
  .rule {
    position: absolute; left: 50%; width: 198px; height: 3px;
    margin-left: -99px; background: var(--gold);
  }
  .rule--month { top: 656px; }
  .rule--year-top { top: 836px; }
  .rule--year-bottom { top: 893px; }
  .details__label { font-weight: 700; font-size: 21px; color: var(--gold); letter-spacing: 1px; }
  .details__value { font-weight: 400; font-size: 21px; color: var(--white); letter-spacing: 0.5px; }
  .details__label--time { top: 970px; }
  .details__value--time { top: 996px; }
  .details__label--location { top: 1057px; }
  .details__value--location { top: 1083px; }
</style>
</head>
<body>
<main class="flyer">
  <div class="flyer__artwork" role="img" aria-label="Faint dark illustration of a mechanical robotic head behind the text"></div>
  <div class="flyer__frame"></div>

  <header class="brand">
    <span class="brand__dot"></span>
    <span class="brand__name">Kinetic Harbor Wellness</span>
  </header>

  <h1>
    <span class="centered headline__grand">GRAND</span>
    <span class="centered headline__opening">OPENING</span>
  </h1>

  <p class="centered date__weekday">THURSDAY</p>
  <p class="centered date__month">JUNE</p>
  <span class="rule rule--month"></span>
  <p class="centered date__day">1</p>
  <span class="rule rule--year-top"></span>
  <p class="centered date__year">2023</p>
  <span class="rule rule--year-bottom"></span>

  <p class="centered details__label details__label--time">TIME</p>
  <p class="centered details__value details__value--time">12pm-6pm</p>
  <p class="centered details__label details__label--location">LOCATION</p>
  <p class="centered details__value details__value--location">58274 Pellham Ave, Bloomfield Hills, MI 48519</p>
</main>
</body>
</html>
```